Classy, Elegant, Simple Business Card Design

Looking to have a classy, simple, and elegant design. Want a top notch designed business card. I really like the look of the new torvane credit card. I also like the design I attached. I am trying to reach 21-29 year old females for booking us for there wedding or event. We offer Disc Jockey Service, Photo Booth Rentals, and Uplighting .

Target Market(s)

21-28 year old females

Contact Information for Business Card

Has to have logo, website, email, and phone number

Font styles to use
Other font styles liked:
• open to font choice, modern, clean
Designer to choose
33a6d7
0791cd
0555a3
ffffff

Requirements
Must have
• Has to have logo, website, email, and phone number
Nice to have
• I really like the design of the new torvane credit card. I also included my logo and some designs I like
Should not have
• clutter or too much info

```html
<!DOCTYPE html>
<html lang="en">
<head>
<meta charset="utf-8">
<title>Tidelight Event Group – Business Card</title>
<link href="https://fonts.googleapis.com/css2?family=Poppins:wght@300;400;500;600&display=swap" rel="stylesheet">
<style>
  :root {
    --sky: #33a6d7;
    --blue: #0791cd;
    --navy: #0555a3;
    --white: #ffffff;
    --ink: #2b2f38;
    --grey: #9aa1ab;
    --backdrop: #ececee;
  }
  * { box-sizing: border-box; margin: 0; padding: 0; }
  html, body { width: 1200px; height: 885px; overflow: hidden; }
  body {
    background: var(--backdrop);
    font-family: "Poppins", sans-serif;
    position: relative;
  }
  .card {
    position: absolute;
    width: 560px;
    height: 320px;
    background: var(--white);
    box-shadow: 0 10px 28px rgba(0,0,0,0.18);
    overflow: hidden;
  }
  /* Front */
  .card-front { left: 90px; top: 90px; }
  .front-brand {
    position: absolute;
    left: 0; right: 0; top: 96px;
    text-align: center;
  }
  .brand-name {
    font-weight: 500;
    font-size: 44px;
    letter-spacing: 3px;
    color: var(--navy);
    line-height: 1;
  }
  .brand-sub {
    margin-top: 10px;
    font-weight: 300;
    font-size: 15px;
    letter-spacing: 9px;
    color: var(--grey);
    padding-left: 9px;
  }
  .services {
    position: absolute;
    left: 0; right: 0; bottom: 42px;
    text-align: center;
    font-size: 13px;
    color: var(--ink);
  }
  .services .dot { color: var(--blue); margin: 0 4px; }

  /* Back */
  .card-back { left: 550px; top: 470px; }
  .back-panel {
    position: absolute;
    left: 0; top: 0; bottom: 0;
    width: 46%;
    background: linear-gradient(160deg, var(--blue), var(--sky));
    color: var(--white);
    padding: 74px 0 0 30px;
  }
  .back-brand .brand-name { color: var(--white); font-size: 24px; letter-spacing: 1.5px; }
  .back-brand .brand-sub { color: var(--white); font-size: 9px; letter-spacing: 5px; margin-top: 4px; padding-left: 0; }
  .person { margin-top: 26px; }
  .person-name { font-weight: 600; font-size: 19px; line-height: 1.1; }
  .person-role { font-size: 12px; font-weight: 400; }
  .contacts { list-style: none; margin-top: 18px; font-size: 11.5px; }
  .contacts li { display: flex; align-items: center; gap: 8px; line-height: 1.55; }
  .contacts svg { width: 12px; height: 12px; flex: none; }
  .back-mark {
    position: absolute;
    left: 46%; right: 10px; top: 0; bottom: 0;
    display: flex; align-items: center; justify-content: center; gap: 12px;
  }
  .back-mark .mark-dot {
    width: 22px; height: 22px; border-radius: 50%;
    background: var(--blue);
  }
  .back-mark .mark-name {
    font-weight: 500;
    font-size: 38px;
    color: var(--blue);
    letter-spacing: 1px;
  }
  .edge-stripe {
    position: absolute;
    right: 0; top: 0; bottom: 0;
    width: 10px;
    background: var(--blue);
  }
</style>
</head>
<body>

<section class="card card-front">
  <div class="front-brand">
    <div class="brand-name">TIDELIGHT</div>
    <div class="brand-sub">EVENT GROUP</div>
  </div>
  <p class="services">Disc Jockey Service<span class="dot">•</span>Photo Booth Rentals<span class="dot">•</span>Uplighting .</p>
</section>

<section class="card card-back">
  <div class="back-panel">
    <div class="back-brand">
      <div class="brand-name">TIDELIGHT</div>
      <div class="brand-sub">EVENT GROUP</div>
    </div>
    <div class="person">
      <div class="person-name">Daniel Reeve</div>
      <div class="person-role">President</div>
    </div>
    <ul class="contacts">
      <li>
        <svg viewBox="0 0 24 24" aria-hidden="true"><path fill="#fff" d="M6.6 10.8a15 15 0 0 0 6.6 6.6l2.2-2.2c.3-.3.7-.4 1-.2 1.1.4 2.3.6 3.6.6.6 0 1 .4 1 1V20c0 .6-.4 1-1 1A17 17 0 0 1 3 4c0-.6.4-1 1-1h3.5c.6 0 1 .4 1 1 0 1.3.2 2.5.6 3.6.1.3 0 .7-.2 1z"/></svg>
        555-014-2270
      </li>
      <li>
        <svg viewBox="0 0 24 24" aria-hidden="true"><rect x="2" y="5" width="20" height="14" rx="1.5" fill="#fff"/><path d="M3 6l9 7 9-7" fill="none" stroke="#0791cd" stroke-width="1.8"/></svg>
        info@tidelightevents.com
      </li>
      <li>
        <svg viewBox="0 0 24 24" aria-hidden="true"><circle cx="12" cy="12" r="10" fill="#fff"/><path d="M2 12h20M12 2c3 3 3 17 0 20M12 2c-3 3-3 17 0 20" fill="none" stroke="#0791cd" stroke-width="1.5"/></svg>
        www.tidelightevents.com
      </li>
    </ul>
  </div>
  <div class="back-mark">
    <span class="mark-dot"></span>
    <span class="mark-name">Tidelight</span>
  </div>
  <div class="edge-stripe"></div>
</section>

</body>
</html>
```